Velundra Jobs portal

Velundra Jobs is a job portal connecting job seekers and companies offering part time jobs in the Mena region, starting in the UAE. We would like to see designs that use the color blue. We have attached images to give an idea what the website should look like. When a company posts a job the job seekers are not allowed to see which company has posted a job. There should also be a coinvex gateway. On the landing page we want a catching picture that we will send.

Target Market(s)

Students and promotional workers

Logo Text

Velundra Jobs

Coding

Coded - Design and coding required

Number of Pages Required

4 page

Font styles to use
Sans Serif

Colors
33a6d7
0692cd
85cae6

```html
<!DOCTYPE html>
<html lang="en">
<head>
<meta charset="utf-8">
<title>Velundra Jobs</title>
<link href="https://fonts.googleapis.com/css2?family=Open+Sans:wght@400;600&display=swap" rel="stylesheet">
<style>
  :root {
    --bg-light: #b9c4c8;
    --bg-mid: #5d676c;
    --bg-dark: #2a2f33;
    --white: #ffffff;
    --teal: #3fb8c0;
    --brand-blue: #33a6d7;
    --btn-blue-top: #33b0f5;
    --btn-blue-bottom: #0692e8;
    --btn-grey-top: #8a8c8e;
    --btn-grey-bottom: #5c5e60;
    --footer: #172f45;
    --footer-text: #e6ecf2;
  }
  * { margin: 0; padding: 0; box-sizing: border-box; }
  html, body { width: 1200px; height: 909px; overflow: hidden; }
  body {
    font-family: "Open Sans", Arial, sans-serif;
    color: var(--white);
    position: relative;
    background:
      radial-gradient(ellipse 520px 420px at 560px 260px, var(--bg-light) 0%, var(--bg-mid) 50%, transparent 100%),
      linear-gradient(90deg, var(--bg-mid) 0%, var(--bg-dark) 100%);
  }
  .hero-photo {
    position: absolute; left: 0; top: 0; width: 500px; height: 847px;
    background: linear-gradient(180deg, #9aa4a8 0%, #4b5256 30%, #1e2124 60%, #141618 100%);
  }
  .brand-card {
    position: absolute; left: 526px; top: 180px; width: 156px; height: 187px;
    background: var(--white);
    display: flex; flex-direction: column; align-items: center; justify-content: flex-end;
    padding-bottom: 26px;
  }
  .brand-card .mark { width: 46px; height: 46px; background: var(--brand-blue); margin-bottom: 24px; }
  .brand-card .name { color: var(--teal); font-size: 22px; font-weight: 400; }
  .brand-rule {
    position: absolute; left: 526px; top: 366px; width: 558px; height: 4px; background: var(--teal);
  }
  .intro {
    position: absolute; left: 713px; top: 264px; width: 380px;
    font-size: 13.3px; line-height: 26.7px;
  }
  .headline { position: absolute; left: 526px; top: 446px; text-transform: uppercase; }
  .headline .line-1 { font-size: 46px; font-weight: 400; line-height: 54px; letter-spacing: 0.5px; }
  .headline .line-2 { font-size: 60px; font-weight: 600; line-height: 68px; letter-spacing: 0.8px; }
  .headline .line-3 { font-size: 27px; font-weight: 400; line-height: 32px; margin-top: 22px; }
  .actions { position: absolute; left: 532px; top: 687px; display: flex; gap: 20px; }
  .btn {
    width: 167px; height: 48px; display: flex; align-items: center; justify-content: center;
    font-size: 16.5px; font-weight: 600; text-transform: uppercase; color: var(--white);
    text-shadow: 0 1px 1px rgba(0,0,0,0.35);
  }
  .btn-seeker { background: linear-gradient(180deg, var(--btn-blue-top), var(--btn-blue-bottom)); }
  .btn-employer { background: linear-gradient(180deg, var(--btn-grey-top), var(--btn-grey-bottom)); }
  .site-footer {
    position: absolute; left: 0; top: 847px; width: 1200px; height: 62px;
    background: var(--footer); color: var(--footer-text); font-size: 12.5px;
  }
  .site-footer .copyright { position: absolute; left: 51px; top: 22px; }
  .site-footer .links { position: absolute; right: 53px; top: 22px; }
</style>
</head>
<body>
  <div class="hero-photo" role="img" aria-label="Portrait photo of a man in a dark suit with arms folded"></div>

  <div class="brand-card">
    <div class="mark"></div>
    <div class="name">Velundra</div>
  </div>
  <div class="brand-rule"></div>

  <p class="intro">We are providing part time jobs for students in Dubai. If you are a student and have quite free time and want to invest it gaining extra money. So you are int he rigth place</p>

  <div class="headline">
    <div class="line-1">Number one platform</div>
    <div class="line-2">Connecting people</div>
    <div class="line-3">With events companies</div>
  </div>

  <div class="actions">
    <a class="btn btn-seeker">Job Seeker</a>
    <a class="btn btn-employer">Employer</a>
  </div>

  <footer class="site-footer">
    <div class="copyright">Copyright © 2015. VELUNDRA. All rights reserved</div>
    <div class="links">About Us - Terms &amp; Conditions - Site Map</div>
  </footer>
</body>
</html>
```